Beautiful design for wordpress

I need a beautiful, colourful and feminine website. My business is called 'The Velvet Lantern', and I sell crystals, books, CD's, pendulums and other metaphysical items. I also provide Reiki (energy healing).
I want this design to be eye catching and inspire happiness and joy in those who see it. And I would love to see the use of the logo and its colours :)
Please add these on the web design: Home, About, Online store, Blog

Industry/Entity Type

Business

Requirements
Must have
• Colourful and playful, must use the logo somewhere, have the words on a menu saying 'Home, Blog, Online store and about' (or similar to those)And the design must stand out!
Should not have
• grey, brown and other boring colours.

```html
<!DOCTYPE html>
<html lang="en">
<head>
<meta charset="utf-8">
<title>The Velvet Lantern – Crystals &amp; Gifts</title>
<link href="https://fonts.googleapis.com/css2?family=Open+Sans:ital,wght@0,400;0,600;1,400&family=PT+Serif&family=Great+Vibes&display=swap" rel="stylesheet">
<style>
:root{
  --orange:#f7941d;
  --orange-light:#fbb040;
  --orange-dark:#e8780c;
  --green:#8cc63f;
  --green-dark:#6fa52a;
  --red:#e8202a;
  --ink:#444;
  --muted:#888;
  --line:#dcdcdc;
  --charcoal:#555;
  --footer:#f0f0f0;
  --bottom:#3a3a3a;
  --white:#fff;
}
*{box-sizing:border-box;margin:0;padding:0}
html,body{width:765px;height:1200px;overflow:hidden}
body{position:relative;background:var(--white);font-family:"Open Sans",Arial,sans-serif;color:var(--ink)}
.abs{position:absolute}
.header-bg{left:0;top:0;width:765px;height:105px;background:linear-gradient(#fff,#f6f6f6)}
.top-links{top:13px;left:433px;font-size:7.5px;color:#666;display:flex;gap:6px;white-space:nowrap}
.top-links .sep{color:#aaa}
.top-links .sel{margin-left:16px}
.brand{left:86px;top:22px;display:flex;align-items:center;gap:6px}
.brand-dot{width:14px;height:14px;border-radius:50%;background:var(--green)}
.brand-name{font-size:13px;font-weight:600;color:#8a5aa8;line-height:1.1;width:70px}
.search{left:431px;top:46px;width:135px;height:24px;border:1px solid var(--line);background:#fff}
.search span{position:absolute;left:10px;top:6px;font-size:7.5px;font-style:italic;color:#aaa}
.search-btn{right:-1px;top:-1px;width:24px;height:24px;background:var(--green)}
.cart{left:579px;top:35px;width:102px;height:37px;border:1px solid var(--line);background:#fff}
.cart-title{left:12px;top:4px;font-family:"PT Serif",serif;font-size:11.5px;color:#333}
.cart-sum{left:12px;top:21px;font-size:7.5px;color:var(--green-dark)}
.cart-sum b{color:var(--red);font-weight:400}
.nav{left:82px;top:87px;width:600px;height:33px;border-radius:2px;background:linear-gradient(var(--orange-light),var(--orange))}
.nav a{position:absolute;top:13px;font-size:8px;color:#3a2200;text-decoration:none}
.nav .active{left:18px;top:6px;width:46px;height:21px;background:var(--orange-dark);color:#fff;text-align:center;line-height:21px}
.hero{left:82px;top:134px;width:600px;height:241px;background:radial-gradient(ellipse at 72% 55%,#bcd2ea 0%,#6f8fbc 30%,#2c3b69 65%,#1b2146 100%)}
.hero-title{left:14px;top:58px;font-family:"Great Vibes",cursive;font-size:24px;color:#fff}
.hero-text{left:15px;top:102px;width:270px;font-size:8.6px;line-height:16px;color:#fff}
.hero-btn{left:15px;top:149px;width:76px;height:27px;background:var(--orange);color:#3a2200;font-size:7.5px;text-align:center;line-height:27px}
.dots{left:16px;top:218px;display:flex;gap:3px}
.dots i{width:8px;height:8px;border-radius:50%;background:#5a6385}
.dots i.on{background:var(--orange)}
.featured{left:82px;top:409px;width:600px;height:35px;border:1px solid var(--line)}
.featured h2{position:absolute;left:13px;top:11px;font-size:11.5px;font-weight:400;color:#333}
.arrow{top:10px;width:13px;height:14px;background:#666}
.card{width:181px;height:232px;border:1px solid var(--line);background:#fff}
.card .photo{position:absolute;left:10px;top:10px;width:160px;height:106px}
.card .name{position:absolute;left:11px;top:134px;font-size:10px;color:var(--red)}
.card .name em{font-size:7.5px;color:#777}
.card .price{position:absolute;right:10px;top:129px;font-family:"PT Serif",serif;font-size:14.5px;color:#333}
.card .desc{position:absolute;left:11px;top:155px;width:165px;font-size:7.6px;line-height:13px;color:var(--muted)}
.card .add{position:absolute;left:12px;top:193px;width:81px;height:24px;background:var(--green);color:#fff;font-size:8px;font-weight:600;line-height:24px;padding-left:7px}
.card .add svg{position:absolute;right:0;top:0;border-left:1px solid var(--green-dark)}
.card .detail{position:absolute;left:103px;top:193px;width:54px;height:24px;background:var(--charcoal);color:#fff;font-size:8px;text-align:center;line-height:24px}
.footer{left:0;top:994px;width:765px;height:168px;background:var(--footer)}
.col{top:20px}
.col h3{font-size:10.5px;font-weight:400;color:#333;margin-bottom:10px}
.col li{list-style:none;font-size:7.8px;color:#777;line-height:19.2px;padding-left:1px}
.divider{top:22px;width:1px;height:120px;background:#e0e0e0}
.email{left:542px;top:47px;width:140px;height:21px;background:#fff;font-size:7px;font-style:italic;color:#aaa;padding:7px 0 0 10px}
.subscribe{left:636px;top:76px;font-size:8px;color:var(--green-dark)}
.follow{left:543px;top:100px;font-size:10.5px;color:#333}
.social{left:543px;top:122px;display:flex;gap:5px}
.social i{width:17px;height:17px;border-radius:50%;background:#999}
.bottom{left:0;top:1162px;width:765px;height:38px;background:var(--bottom);color:#ddd;font-size:7.3px;text-align:center;line-height:38px}
</style>
</head>
<body>
<div class="abs header-bg"></div>

<div class="abs brand">
  <span class="brand-dot"></span>
  <span class="brand-name">The Velvet Lantern</span>
</div>

<div class="abs top-links">
  <span>Log In</span><span class="sep">|</span><span>Checkout</span><span class="sep">|</span><span>My Wishlist</span><span class="sep">|</span><span>My Account</span>
  <span class="sel">En ˅</span><span>$ ˅</span>
</div>

<div class="abs search"><span>Search...</span>
  <div class="abs search-btn">
    <svg width="24" height="24" viewBox="0 0 24 24"><circle cx="11" cy="11" r="3.3" fill="none" stroke="#fff" stroke-width="1.6"/><line x1="13.4" y1="13.4" x2="15.6" y2="15.6" stroke="#fff" stroke-width="1.8"/></svg>
  </div>
</div>

<div class="abs cart">
  <div class="abs cart-title">My Cart</div>
  <div class="abs cart-sum">0 item(s) - <b>$0.00</b></div>
  <svg class="abs" style="right:9px;top:16px" width="6" height="4" viewBox="0 0 6 4"><path d="M0 0l3 3 3-3" fill="none" stroke="#999"/></svg>
</div>

<nav class="abs nav">
  <a class="active">HOME</a>
  <a style="left:103px">ABOUT</a>
  <a style="left:167px">ONLINE STORE</a>
  <a style="left:264px">BLOG</a>
  <a style="left:323px">CONTACT US</a>
</nav>

<section class="abs hero" role="img" aria-label="Photo of clear quartz crystal points in cool blue light">
  <div class="abs hero-title">Neque porro quisquam est</div>
  <p class="abs hero-text">Excepteur sint occaecat cupidatat non proident, sunt in culpa qui officia deserunt mollit anim id est laborum.</p>
  <div class="abs hero-btn">SHOP NOW!</div>
  <div class="abs dots"><i class="on"></i><i></i><i></i><i></i></div>
</section>

<div class="abs featured">
  <h2>FEATURED PRODUCTS</h2>
  <div class="abs arrow" style="left:559px"><svg width="13" height="14" viewBox="0 0 13 14"><path d="M8 4l-3 3 3 3" fill="none" stroke="#fff" stroke-width="1.4"/></svg></div>
  <div class="abs arrow" style="left:574px"><svg width="13" height="14" viewBox="0 0 13 14"><path d="M5 4l3 3-3 3" fill="none" stroke="#fff" stroke-width="1.4"/></svg></div>
</div>

<!-- product cards -->
<div class="abs card" style="left:82px;top:468px">
  <div class="photo" role="img" aria-label="Photo of a white crystal cluster on purple" style="background:linear-gradient(135deg,#3b2250,#c9c3d6 50%,#6a3d8f)"></div>
  <div class="name">CRYSTALS</div><div class="price">$129.00</div>
  <p class="desc">Excepteur sint occaecat cupidatat non sit proident, sunt in culpa quis.</p>
  <div class="add">Add to Cart<svg width="22" height="24" viewBox="0 0 22 24"><path d="M6 9h2l1.5 5h5l1.5-4H9" fill="none" stroke="#fff" stroke-width="1.3"/><circle cx="10" cy="16" r="1" fill="#fff"/><circle cx="14" cy="16" r="1" fill="#fff"/></svg></div>
  <div class="detail">Detail</div>
</div>
<div class="abs card" style="left:292px;top:468px">
  <div class="photo" role="img" aria-label="Photo of a stack of colourful books" style="background:linear-gradient(#f0a54a,#c7402d 45%,#8a5a2c 80%,#b07a45)"></div>
  <div class="name">BOOKS</div><div class="price">$129.00</div>
  <p class="desc">Excepteur sint occaecat cupidatat non sit proident, sunt in culpa quis.</p>
  <div class="add">Add to Cart<svg width="22" height="24" viewBox="0 0 22 24"><path d="M6 9h2l1.5 5h5l1.5-4H9" fill="none" stroke="#fff" stroke-width="1.3"/><circle cx="10" cy="16" r="1" fill="#fff"/><circle cx="14" cy="16" r="1" fill="#fff"/></svg></div>
  <div class="detail">Detail</div>
</div>
<div class="abs card" style="left:501px;top:468px">
  <div class="photo" role="img" aria-label="Photo of a stack of CD cases" style="background:radial-gradient(ellipse at 50% 50%,#4a4a4a,#bcbcbc 55%,#f2f2f2)"></div>
  <div class="name">CD’S</div><div class="price">$129.00</div>
  <p class="desc">Excepteur sint occaecat cupidatat non sit proident, sunt in culpa quis.</p>
  <div class="add">Add to Cart<svg width="22" height="24" viewBox="0 0 22 24"><path d="M6 9h2l1.5 5h5l1.5-4H9" fill="none" stroke="#fff" stroke-width="1.3"/><circle cx="10" cy="16" r="1" fill="#fff"/><circle cx="14" cy="16" r="1" fill="#fff"/></svg></div>
  <div class="detail">Detail</div>
</div>

<div class="abs card" style="left:82px;top:722px">
  <div class="photo" role="img" aria-label="Photo of gemstone pendulums on gold chains" style="background:linear-gradient(90deg,#dfe6ee,#7aa39e 25%,#a05a55 50%,#b8867a 75%,#dfe6ee)"></div>
  <div class="name">PENDULUMS</div><div class="price">$129.00</div>
  <p class="desc">Excepteur sint occaecat cupidatat non sit proident, sunt in culpa quis.</p>
  <div class="add">Add to Cart<svg width="22" height="24" viewBox="0 0 22 24"><path d="M6 9h2l1.5 5h5l1.5-4H9" fill="none" stroke="#fff" stroke-width="1.3"/><circle cx="10" cy="16" r="1" fill="#fff"/><circle cx="14" cy="16" r="1" fill="#fff"/></svg></div>
  <div class="detail">Detail</div>
</div>
<div class="abs card" style="left:292px;top:722px">
  <div class="photo" role="img" aria-label="Photo of a green stone pendant on a speckled rock" style="background:radial-gradient(circle at 60% 65%,#4f8a86,#a88a6c 35%,#8b6e52)"></div>
  <div class="name">METAPHYSICAL</div><div class="price">$129.00</div>
  <p class="desc">Excepteur sint occaecat cupidatat non sit proident, sunt in culpa quis.</p>
  <div class="add">Add to Cart<svg width="22" height="24" viewBox="0 0 22 24"><path d="M6 9h2l1.5 5h5l1.5-4H9" fill="none" stroke="#fff" stroke-width="1.3"/><circle cx="10" cy="16" r="1" fill="#fff"/><circle cx="14" cy="16" r="1" fill="#fff"/></svg></div>
  <div class="detail">Detail</div>
</div>
<div class="abs card" style="left:501px;top:722px">
  <div class="photo" role="img" aria-label="Photo of a relaxing Reiki energy healing session" style="background:linear-gradient(120deg,#e9c2a8,#f6e3d6 50%,#e8ded4)"></div>
  <div class="name">REIKI <em>(energy healing)</em></div><div class="price">$129.00</div>
  <p class="desc">Excepteur sint occaecat cupidatat non sit proident, sunt in culpa quis.</p>
  <div class="add">Add to Cart<svg width="22" height="24" viewBox="0 0 22 24"><path d="M6 9h2l1.5 5h5l1.5-4H9" fill="none" stroke="#fff" stroke-width="1.3"/><circle cx="10" cy="16" r="1" fill="#fff"/><circle cx="14" cy="16" r="1" fill="#fff"/></svg></div>
  <div class="detail">Detail</div>
</div>

<footer class="abs footer">
  <div class="abs col" style="left:83px"><h3>Information</h3><ul><li>About Us</li><li>Customer Service</li><li>Privacy Policy</li><li>Site Map</li><li>Orders and Returns</li><li>Contact Us</li></ul></div>
  <div class="abs divider" style="left:194px"></div>
  <div class="abs col" style="left:236px"><h3>Why buy from us</h3><ul><li>Shipping &amp; Returns</li><li>Secure Shopping</li><li>International Shipping</li><li>Affiliates</li><li>Group Sales</li></ul></div>
  <div class="abs divider" style="left:353px"></div>
  <div class="abs col" style="left:389px"><h3>My account</h3><ul><li>Sign In</li><li>View Cart</li><li>My Wishlist</li><li>Track My Order</li><li>Help</li></ul></div>
  <div class="abs divider" style="left:498px"></div>
  <div class="abs col" style="left:542px"><h3>Newsletter</h3></div>
  <div class="abs email">Enter your Email...</div>
  <div class="abs subscribe">&gt; Subscribe</div>
  <div class="abs follow">Follow us</div>
  <div class="abs social"><i></i><i></i><i></i><i></i></div>
</footer>

<div class="abs bottom">©2014 The Velvet Lantern. All Right Reserved.</div>
</body>
</html>
```